Redesign of business card for Cedar Ridge Mechanical

We are looking for a new design for our business cards for Cedar Ridge Mechanical. We are a plumbing & HVAC construction company, operating on the West Coast of Canada and USA. Logo attached.
Industry/Entity Type
Construction - Plumbing & HVAC
Contact Information for Business Card
Name, address, phone numbers, email, website address
Look and feel
Each slider illustrates characteristics of the customer's brand and the style your logo design should communicate.

```html
<!DOCTYPE html>
<html lang="en">
<head>
<meta charset="utf-8">
<title>Cedar Ridge Mechanical – Business Card</title>
<link rel="stylesheet" href="https://fonts.googleapis.com/css2?family=Montserrat:wght@400;500;700&display=swap">
<style>
  :root {
    --backdrop: #8a6c4c;
    --card-white: #ffffff;
    --ink: #1f1f1f;
    --ink-soft: #2a2a2a;
    --band-dark: #2b2b2b;
    --band-grey: #666666;
    --back-black: #0c0c0c;
    --text-light: #ffffff;
  }
  * { margin: 0; padding: 0; box-sizing: border-box; }
  html, body {
    width: 900px; height: 1200px; overflow: hidden;
    background: var(--backdrop);
    font-family: "Montserrat", Arial, sans-serif;
  }
  .card {
    position: absolute; left: 80px; width: 742px; height: 440px;
    border-radius: 22px; overflow: hidden;
    box-shadow: 0 6px 16px rgba(0,0,0,0.35);
  }
  .card--front { top: 131px; background: var(--card-white); }
  .card--back { top: 638px; background: var(--back-black); }

  .brand-name {
    position: absolute; left: 0; right: 0; top: 62px; height: 160px;
    display: flex; justify-content: center; align-items: center; gap: 22px;
    color: var(--ink); font-weight: 700;
  }
  .brand-name .mark { width: 74px; height: 74px; background: var(--ink); flex: none; }
  .brand-name .words { font-size: 46px; line-height: 52px; letter-spacing: 1px; }

  .person { position: absolute; right: 410px; top: 272px; text-align: right; color: var(--ink); }
  .person__name { font-weight: 700; font-size: 24px; line-height: 30px; }
  .person__title { font-weight: 400; font-size: 16px; line-height: 24px; }

  .divider { position: absolute; left: 356px; top: 267px; width: 2px; height: 82px; background: var(--ink); }

  .contacts { position: absolute; left: 374px; top: 259px; list-style: none; color: var(--ink-soft); }
  .contacts li { display: flex; align-items: center; height: 30px; font-size: 16px; }
  .contacts svg { width: 14px; height: 14px; margin-right: 12px; fill: var(--ink-soft); flex: none; }

  .address-band { position: absolute; left: 0; top: 371px; width: 742px; height: 34px; }
  .address-text {
    position: absolute; left: 0; width: 540px; top: 371px; height: 34px;
    display: flex; align-items: center; justify-content: center;
    color: var(--text-light); font-size: 16px;
  }

  .monogram-pattern { position: absolute; inset: 0; width: 742px; height: 440px; }
  .back-name {
    position: absolute; left: 530px; top: 310px; width: 130px;
    color: var(--text-light); font-weight: 700; font-size: 14px; line-height: 18px;
    text-align: center; letter-spacing: 0.5px;
  }
</style>
</head>
<body>

<section class="card card--front">
  <div class="brand-name">
    <span class="mark"></span>
    <span class="words">CEDAR RIDGE<br>MECHANICAL</span>
  </div>

  <div class="person">
    <div class="person__name">Daniel Moore</div>
    <div class="person__title">Managing Director</div>
  </div>

  <div class="divider"></div>

  <ul class="contacts">
    <li>
      <svg viewBox="0 0 24 24"><path d="M6.6 10.8a15.1 15.1 0 0 0 6.6 6.6l2.2-2.2a1 1 0 0 1 1-.25 11.4 11.4 0 0 0 3.6.57 1 1 0 0 1 1 1V20a1 1 0 0 1-1 1A17 17 0 0 1 3 4a1 1 0 0 1 1-1h3.5a1 1 0 0 1 1 1c0 1.25.2 2.45.57 3.57a1 1 0 0 1-.25 1z"/></svg>
      888.555.0142
    </li>
    <li>
      <svg viewBox="0 0 24 24"><rect x="2" y="5" width="20" height="14" rx="1"/><path d="M2 6l10 7 10-7" stroke="#fff" stroke-width="1.8" fill="none"/></svg>
      info@cedarridgemechanical.com
    </li>
    <li>
      <svg viewBox="0 0 24 24"><circle cx="12" cy="12" r="10"/><path d="M2 12h20M12 2c3 3 3 17 0 20M12 2c-3 3-3 17 0 20" stroke="#fff" stroke-width="1.6" fill="none"/></svg>
      www.cedarridgemechanical.com
    </li>
  </ul>

  <svg class="address-band" viewBox="0 0 742 34" aria-hidden="true">
    <polygon points="0,0 545,0 527,34 0,34" fill="var(--band-dark)"/>
    <polygon points="555,0 742,0 742,34 537,34" fill="var(--band-grey)"/>
  </svg>
  <div class="address-text">240 Harbor View Road Salem, OR 97301</div>
</section>

<section class="card card--back">
  <svg class="monogram-pattern" viewBox="0 0 742 440" role="img" aria-label="Repeating gloss monogram pattern across the card back">
    <defs>
      <linearGradient id="sheen" x1="0" y1="0" x2="1" y2="0.4">
        <stop offset="0" stop-color="#5a5a5a"/>
        <stop offset="0.4" stop-color="#1c1c1c"/>
        <stop offset="1" stop-color="#0c0c0c"/>
      </linearGradient>
    </defs>
    <rect width="742" height="440" fill="url(#sheen)"/>
  </svg>
  <div class="back-name">CEDAR RIDGE MECHANICAL</div>
</section>

</body>
</html>
```